creation of a business card design for a company specializing in the creation...

I would like to create a design for a professional business card on a black background and with the company's colors (I am attaching some files: including the logo in horizontal and centered format, I am also attaching a recent project design a T-shirt, this is the one I chose to give you an idea of my preferences.

we are in the process of developing a new website design, it is still in the development phase but it can be viewed at the following address: www.vantrelmo.be to give you other ideas about the company
you will see for yourself the subject of my main activity: company specializing in the construction of stairs

I would like a business card that stands out from the rest with a unique design

here is the informations
Name: Lucien Barthel
Function: Manager
Address: Rue Moulinet du Parc 42
7180 Montreval
telephone: +32 468 219 804
email: info@rx7p.be
website: rx7p. be
social networks: Facebook, YouTube, TikTok, Instagram

Target Market(s)

customer who wants to have a beautiful staircase built

Industry/Entity Type

contruction d'escalier

Contact Information for Business Card

Adresse. Numero de telephone, site web, le texte : "Createur d'escalier", logo recto-verso, icone des reseaux sociaux

Requirements
Must have
• the mention: Stair creator
Nice to have
• an illustration of a designer staircase
Should not have
• do not distort the logo

```html
<!DOCTYPE html>
<html lang="en">
<head>
<meta charset="utf-8">
<title>Vantrelmo business card</title>
<link rel="stylesheet" href="https://fonts.googleapis.com/css2?family=Lato:wght@400;700&display=swap">
<style>
  :root {
    --backdrop: #2a292a;
    --card: #1d1d1e;
    --blue: #5a8fb4;
    --blue-light: #a9cbe2;
    --blue-deep: #3f6f92;
    --text: #c9c9c9;
  }
  * { box-sizing: border-box; margin: 0; padding: 0; }
  html, body { width: 1200px; height: 939px; overflow: hidden; }
  body {
    background: var(--backdrop);
    font-family: "Lato", sans-serif;
    position: relative;
  }
  .card {
    position: absolute;
    width: 560px;
    height: 360px;
    background: var(--card);
    border-radius: 22px;
    overflow: hidden;
    box-shadow: 0 14px 30px rgba(0,0,0,.45);
  }
  .card--front { left: 60px; top: 70px; }
  .card--back { left: 580px; top: 510px; }

  .stair-art {
    position: absolute;
    background: linear-gradient(160deg, var(--blue-light) 0%, var(--blue) 55%, var(--blue-deep) 100%);
    opacity: .9;
  }
  .card--front .stair-art {
    left: 0; top: 0; width: 230px; height: 360px;
    clip-path: polygon(70% 0, 100% 0, 62% 45%, 40% 72%, 30% 100%, 0 100%, 0 68%, 25% 38%);
  }
  .card--back .stair-art {
    right: 0; top: 0; width: 360px; height: 250px;
    clip-path: polygon(0 0, 55% 0, 80% 18%, 100% 48%, 100% 100%, 82% 100%, 70% 62%, 48% 35%, 15% 18%);
  }

  .contact {
    position: absolute;
    right: 36px; top: 40px;
    text-align: right;
  }
  .contact__name {
    color: var(--blue);
    font-weight: 700;
    font-size: 24px;
    letter-spacing: .5px;
    text-transform: uppercase;
  }
  .contact__role {
    color: var(--text);
    font-size: 15px;
    margin-top: 2px;
  }
  .contact__rule {
    width: 24px; height: 2px;
    background: var(--blue);
    margin: 12px 0 22px auto;
  }
  .contact__line {
    display: flex;
    justify-content: flex-end;
    align-items: center;
    gap: 10px;
    color: var(--text);
    font-size: 15px;
    line-height: 22px;
  }
  .contact__line svg { width: 12px; height: 12px; fill: var(--blue); flex: none; }
  .contact__line .spacer { width: 12px; flex: none; }
  .social {
    display: flex; justify-content: flex-end; gap: 6px;
    margin-top: 22px;
  }
  .social span {
    width: 24px; height: 24px; border-radius: 50%;
    background: var(--blue);
  }

  .brand {
    position: absolute;
    left: 60px; bottom: 60px;
  }
  .brand__name {
    color: var(--text);
    font-weight: 400;
    font-size: 48px;
    line-height: 1;
  }
  .brand__tagline {
    color: var(--text);
    font-size: 15px;
    margin-top: 10px;
  }
</style>
</head>
<body>

<section class="card card--front" aria-label="Card front">
  <div class="stair-art" role="img" aria-label="Illustration of floating blue staircase steps"></div>
  <div class="contact">
    <p class="contact__name">Lucien Barthel</p>
    <p class="contact__role">Manager</p>
    <div class="contact__rule"></div>
    <p class="contact__line">Rue Moulinet du Parc 42
      <svg viewBox="0 0 12 12"><path d="M6 0a4 4 0 0 0-4 4c0 3 4 8 4 8s4-5 4-8a4 4 0 0 0-4-4zm0 5.5A1.5 1.5 0 1 1 6 2.5a1.5 1.5 0 0 1 0 3z"/></svg></p>
    <p class="contact__line">7180 Montreval<span class="spacer"></span></p>
    <p class="contact__line">+32 468 219 804
      <svg viewBox="0 0 12 12"><path d="M2.5 0.5l2 2-1 1.5a7 7 0 0 0 4.5 4.5l1.5-1 2 2-1.5 2C5 11 1 7 .5 2z"/></svg></p>
    <p class="contact__line">info@rx7p.be
      <svg viewBox="0 0 12 12"><path d="M0 2h12v8H0zM1 3l5 3.5L11 3v-.2H1z" fill-rule="evenodd"/></svg></p>
    <p class="contact__line">rx7p.be
      <svg viewBox="0 0 12 12"><path d="M6 0a6 6 0 1 0 0 12A6 6 0 0 0 6 0zm0 1.2c.8 0 1.6 2 1.7 4.2H4.3C4.4 3.2 5.2 1.2 6 1.2zM4.3 6.6h3.4C7.6 8.8 6.8 10.8 6 10.8s-1.6-2-1.7-4.2z"/></svg></p>
    <div class="social" role="img" aria-label="Social network links">
      <span></span><span></span><span></span><span></span>
    </div>
  </div>
</section>

<section class="card card--back" aria-label="Card back">
  <div class="stair-art" role="img" aria-label="Illustration of floating blue staircase steps"></div>
  <div class="brand">
    <p class="brand__name">Vantrelmo</p>
    <p class="brand__tagline">Original staircases</p>
  </div>
</section>

</body>
</html>
```